Coastline Premier Retreats Business Card Design

Design a business card for Coastline Premier Retreats. Look at the website for colors and reference. Card should have logo, name, title, office number, mobile number, email, URL and a tagline like, "Luxury Hotel & Resort Email Marketing" (This might change).

https://www.coastlinepremierretreats.example

The rest I will leave up to your imagination.

Contact Information for Business Card

Logo, name, title, office number, mobile number, email, URL and a tagline like, "Luxury Hotel & Resort Email Marketing" (This might change).

```html
<!DOCTYPE html>
<html lang="en">
<head>
<meta charset="utf-8">
<title>Coastline Premier Retreats Business Card</title>
<link rel="stylesheet" href="https://fonts.googleapis.com/css2?family=Arimo:wght@400;700&display=swap">
<style>
  :root {
    --ink: #0b0b0b;
    --paper: #ffffff;
    --accent: #f07622;
    --stage: #e9eaec;
    --text-dark: #111111;
  }
  * { margin: 0; padding: 0; box-sizing: border-box; }
  html, body {
    width: 1200px; height: 900px; overflow: hidden;
    background: var(--stage);
    font-family: "Arimo", Arial, sans-serif;
  }
  .canvas { position: relative; width: 1200px; height: 900px; }

  .card {
    position: absolute; width: 700px; height: 400px; overflow: hidden;
    box-shadow: 0 6px 18px rgba(0,0,0,0.12);
  }

  /* Front */
  .card--front { left: 90px; top: 40px; background: var(--ink); }
  .front__brand {
    position: absolute; left: 0; right: 0; top: 105px;
    display: flex; align-items: center; justify-content: center; gap: 18px;
  }
  .brand-square { width: 26px; height: 26px; background: var(--accent); flex: none; }
  .front__name {
    color: var(--paper); font-weight: 700; font-size: 40px;
    letter-spacing: 2px; text-transform: uppercase; line-height: 1.05;
    text-align: left;
  }
  .front__band {
    position: absolute; left: 0; right: 0; top: 282px; height: 64px;
    background: var(--accent);
    display: flex; align-items: center; justify-content: center;
  }
  .front__tagline { color: var(--paper); font-size: 24px; font-weight: 400; }

  /* Back */
  .card--back { left: 410px; top: 470px; background: var(--paper); }
  .back__brand {
    position: absolute; left: 34px; top: 128px; width: 240px;
    display: flex; align-items: center; gap: 10px;
  }
  .back__brand .brand-square { width: 16px; height: 16px; }
  .back__name {
    color: var(--text-dark); font-weight: 700; font-size: 18px;
    letter-spacing: 1px; text-transform: uppercase; line-height: 1.15;
    white-space: nowrap;
  }
  .back__divider {
    position: absolute; left: 290px; top: 80px; width: 2px; height: 170px;
    background: var(--accent);
  }
  .back__details { position: absolute; left: 308px; top: 84px; width: 370px; }
  .person__name {
    color: var(--accent); font-weight: 700; font-size: 26px;
    text-transform: uppercase; letter-spacing: 0.5px; white-space: nowrap;
  }
  .person__title {
    color: var(--text-dark); font-size: 17px; text-transform: uppercase;
    margin-top: 4px; letter-spacing: 0.5px; white-space: nowrap;
  }
  .contact-list { list-style: none; margin-top: 16px; }
  .contact-list li {
    display: flex; align-items: center; gap: 10px;
    font-size: 15px; color: var(--text-dark); margin-bottom: 8px;
    white-space: nowrap;
  }
  .contact-list svg { width: 17px; height: 17px; flex: none; }
  .back__stripe { position: absolute; left: 0; bottom: 0; width: 700px; height: 90px; }
</style>
</head>
<body>
<main class="canvas">

  <section class="card card--front" aria-label="Card front">
    <div class="front__brand">
      <span class="brand-square"></span>
      <div class="front__name">Coastline<br>Premier Retreats</div>
    </div>
    <div class="front__band">
      <p class="front__tagline">Luxury Hotel &amp; Resort Email Marketing</p>
    </div>
  </section>

  <section class="card card--back" aria-label="Card back">
    <div class="back__brand">
      <span class="brand-square"></span>
      <div class="back__name">Coastline<br>Premier Retreats</div>
    </div>

    <div class="back__divider"></div>

    <div class="back__details">
      <h1 class="person__name">Daniel Moreau</h1>
      <p class="person__title">Managing Director</p>
      <ul class="contact-list">
        <li>
          <svg viewBox="0 0 24 24" aria-hidden="true"><path fill="#f07622" d="M3 9c0-3 4-5 9-5s9 2 9 5l-1 2-4-1V8c-2-.6-6-.6-8 0v2l-4 1zM6 13h12l2 7H4z"/></svg>
          <span>555.014.2200</span>
        </li>
        <li>
          <svg viewBox="0 0 24 24" aria-hidden="true"><rect x="6" y="2" width="12" height="20" rx="2" fill="none" stroke="#f07622" stroke-width="2"/><circle cx="12" cy="18" r="1.2" fill="#f07622"/></svg>
          <span>555.019.3480</span>
        </li>
        <li>
          <svg viewBox="0 0 24 24" aria-hidden="true"><rect x="2" y="5" width="20" height="14" fill="#f07622"/><path d="M2 5l10 8 10-8" fill="none" stroke="#fff" stroke-width="1.6"/></svg>
          <span>dmoreau@coastlinepremierretreats.example</span>
        </li>
      </ul>
    </div>

    <svg class="back__stripe" viewBox="0 0 700 90" preserveAspectRatio="none" aria-hidden="true">
      <polygon points="0,62 545,62 560,34 700,34 700,48 572,48 560,90 0,90" fill="#0b0b0b"/>
      <polygon points="568,30 700,30 700,0 585,0" fill="#f07622"/>
    </svg>
  </section>

</main>
</body>
</html>
```